Physiotherapy Referral Pad

-Need a referral pad for physiotherapy to be provided to doctors' offices. I would like it to be simple, not too cluttered and sharp looking so doctors can quickly complete it for clients.

-I have attached my logo which I would like to include. I have also included my business cards to keep the style, font, colors etc consistent.

-I would like to include my slogan
From Our Home To Yours

-I would like it to include services options with tick boxes for Mobile, Clinic, Telehealth, NRPDLA

-I would like for it to say Call to Book or Book Online

-I would like it to include my clinic address:
472 Marrow Crescent
Whitehorse, YT
Y2B3K9

-I would like it to include my contact info:
Glen Ostrow BSc(kin), MPT, CAFCI, IMS
(867)555-0142
physio@ostrowtherapy.ca

-I would like lines for the following:
Patient Name:
Diagnosis/Recommendations:
(extra lines to fill out patient info)

Physician Signature
Date

Target Market(s)

Physicians to refer clients to physiotherapy

Industry/Entity Type

Physical Therapy

Requirements
Must have
• Clean, concise, easy to look at and find pertinant categories for physicians
Nice to have
• Ostrow Therapy color scheme. Please see business cards and website as needed
Should not have
• Not too cluttered or wordy

```html
<!DOCTYPE html>
<html lang="en">
<head>
<meta charset="utf-8">
<title>Ostrow Therapy Referral Pad</title>
<link rel="stylesheet" href="https://fonts.googleapis.com/css2?family=Cinzel:wght@600;700&family=Libre+Baskerville:wght@700&family=Montserrat:wght@400&display=swap">
<style>
  :root {
    --navy: #233b8a;
    --green: #1a5a32;
    --ink: #3a3a3a;
    --rule: #4a4a4a;
    --paper: #fafafa;
    --backdrop: #dedede;
  }
  * { margin: 0; padding: 0; box-sizing: border-box; }
  html, body { width: 1200px; height: 800px; overflow: hidden; background: var(--backdrop); }
  .pad {
    position: absolute; left: 330px; top: 20px; width: 540px; height: 760px;
    background: var(--paper); box-shadow: 0 10px 30px rgba(0,0,0,.18);
  }
  .top-band {
    position: absolute; left: 0; top: 0; width: 100%; height: 31px; background: var(--navy);
    color: #fff; font: 600 14px/31px "Cinzel", serif; letter-spacing: 2.5px; text-align: center;
  }
  .brand {
    position: absolute; left: 45px; top: 82px; display: flex; align-items: center; gap: 7px;
    color: var(--green); font: 700 17px/1 "Libre Baskerville", serif;
  }
  .brand-mark { width: 12px; height: 12px; background: var(--navy); }
  .contact { position: absolute; left: 351px; top: 56px; font: 400 10.5px/1.3 "Montserrat", sans-serif; color: var(--ink); font-style: normal; }
  .contact .gap { height: 8px; }
  .contact .row { display: flex; align-items: center; gap: 3px; line-height: 14px; }
  .contact svg { width: 9px; height: 9px; flex: none; }
  .practitioner { position: absolute; left: 0; width: 100%; top: 176px; text-align: center; font-family: "Libre Baskerville", serif; font-weight: 700; }
  .practitioner-name { color: var(--green); font-size: 27px; letter-spacing: .5px; line-height: 1.2; }
  .credentials { color: var(--navy); font-size: 12px; margin-top: 1px; }
  .services { position: absolute; left: 0; width: 100%; top: 239px; display: flex; justify-content: center; gap: 8px;
    font: 700 14px/1 "Libre Baskerville", serif; color: var(--navy); }
  .services span { display: flex; align-items: center; gap: 5px; }
  .services i { width: 12px; height: 12px; border: 1.5px solid var(--ink); display: inline-block; }
  .field { position: absolute; left: 55px; right: 58px; display: flex; align-items: flex-end; gap: 8px;
    color: var(--navy); font: 700 13px/1 "Libre Baskerville", serif; letter-spacing: .3px; }
  .field .line { flex: 1; height: 1px; background: var(--rule); margin-bottom: 1px; }
  .field .sc { font-size: 10.5px; }
  .rule { position: absolute; height: 1px; background: var(--rule); left: 55px; right: 58px; }
  .bottom-band {
    position: absolute; left: 0; bottom: 0; width: 465px; height: 43px; background: var(--navy);
    clip-path: polygon(0 0, 100% 0, 92% 100%, 0 100%);
  }
  .slogan {
    position: absolute; left: 0; bottom: 0; width: 460px; height: 43px; text-align: center;
    color: #fff; font: 700 18px/43px "Cinzel", serif; letter-spacing: 3px;
  }
</style>
</head>
<body>
  <main class="pad">
    <header class="top-band">Call to Book or Book Online</header>

    <div class="brand"><span class="brand-mark"></span>Ostrow Therapy</div>

    <address class="contact">
      <div>472 Marrow Crescent</div>
      <div>Whitehorse, YT Y2B3K9</div>
      <div class="gap"></div>
      <div class="row"><svg viewBox="0 0 10 10"><circle cx="5" cy="5" r="5" fill="#1a5a32"/><path d="M3 2.5l1 1-.6.8a4 4 0 0 0 2.3 2.3l.8-.6 1 1-.8.8C4.5 7.5 2.5 5.5 2.2 3.3z" fill="#fff"/></svg>(867)555-0142</div>
      <div class="row"><svg viewBox="0 0 10 10"><circle cx="5" cy="5" r="5" fill="#1a5a32"/><rect x="2.6" y="3.2" width="4.8" height="3.6" fill="none" stroke="#fff" stroke-width=".8"/><path d="M2.6 3.2L5 5.2l2.4-2" fill="none" stroke="#fff" stroke-width=".8"/></svg>physio@ostrowtherapy.ca</div>
      <div class="row"><svg viewBox="0 0 10 10"><circle cx="5" cy="5" r="5" fill="#1a5a32"/><circle cx="5" cy="5" r="2.5" fill="none" stroke="#fff" stroke-width=".8"/><path d="M2.5 5h5M5 2.5v5" stroke="#fff" stroke-width=".6"/></svg>www.ostrowtherapy.ca</div>
    </address>

    <section class="practitioner">
      <h1 class="practitioner-name">GLEN OSTROW</h1>
      <p class="credentials">BSC(KIN), MPT, CAFCI, IMS</p>
    </section>

    <div class="services">
      <span><i></i>MOBILE</span>
      <span><i></i>CLINIC</span>
      <span><i></i>TELEHEALTH</span>
      <span><i></i>NRPDLA</span>
    </div>

    <div class="field" style="top:340px"><span>PATIENT NAME:</span><span class="line"></span></div>
    <div class="rule" style="top:398px"></div>

    <div class="field" style="top:430px"><span>D<span class="sc">IAGNOSIS</span>/R<span class="sc">ECOMMENDATIONS</span>:</span><span class="line"></span></div>
    <div class="rule" style="top:487px"></div>
    <div class="rule" style="top:532px;left:58px;right:55px"></div>

    <div class="field" style="top:605px;right:57px"><span>P<span class="sc">HYSICIAN</span> S<span class="sc">IGNATURE</span></span><span class="line"></span></div>
    <div class="field" style="top:650px;right:57px"><span>D<span class="sc">ATE</span></span><span class="line"></span></div>

    <div class="bottom-band"></div>
    <footer class="slogan">From Our Home to Yours</footer>
  </main>
</body>
</html>
```